Basic business card

use my newly created logo - and the phrases (Quicker Analog Launches & Verified Unit Bring-up for Every Wafer) - and my new email domain / ID - use at conferences / tradeshows

Industry/Entity Type

semiconductor

Contact Information for Business Card

Daniel K Forde, Owner, communicate via Logo - Lower COT - Cost of Test, Accelerated NPI - New Product Introduction, phone +1 555 613 0946, Harlow Springs, Oregon, USA, daniel.forde@qal-vub.com

Font styles to use
Sans Serif

Requirements
Nice to have
• re-use my logo created via Pixel Harbor last August (#7315926)

```html
<!DOCTYPE html>
<html lang="en">
<head>
<meta charset="utf-8">
<title>QAL-VUB Business Card</title>
<link rel="stylesheet" href="https://fonts.googleapis.com/css2?family=Montserrat:wght@400;500;700&display=swap">
<style>
  :root {
    --slate: #4b5a75;
    --slate-deep: #3f4d66;
    --paper: #ffffff;
    --stage: #1d1d1d;
    --green: #7bbb2a;
    --orange: #f39419;
    --blue: #1f78c4;
    --ink-light: #ffffff;
  }
  * { box-sizing: border-box; margin: 0; padding: 0; }
  html, body {
    width: 1200px; height: 988px; overflow: hidden;
    background: var(--stage);
    font-family: "Montserrat", sans-serif;
  }
  .canvas { position: relative; width: 1200px; height: 988px; }
  .card {
    position: absolute; width: 620px; height: 354px;
    border-radius: 22px; overflow: hidden;
    background: var(--slate);
    box-shadow: 0 12px 30px rgba(0,0,0,.5);
  }
  .card--front { left: 40px; top: 80px; }
  .card--back { left: 540px; top: 554px; }

  .brand { display: flex; align-items: center; gap: 14px; font-weight: 500; letter-spacing: 3px; }
  .brand__mark { width: 22px; height: 22px; background: var(--green); }

  .card--front .brand {
    position: absolute; left: 0; right: 0; top: 118px;
    justify-content: center; color: var(--ink-light); font-size: 60px;
  }
  .card--front .tagline {
    position: absolute; left: 0; right: 0; bottom: 64px; text-align: center;
    color: var(--ink-light); font-size: 15.5px; letter-spacing: 1px;
  }

  .card--back .curve { position: absolute; inset: 0; width: 620px; height: 354px; }
  .card--back .brand {
    position: absolute; left: 300px; top: 46px;
    color: var(--slate-deep); font-size: 46px;
  }
  .contact { position: absolute; left: 44px; bottom: 30px; color: var(--ink-light); }
  .contact__name { font-weight: 700; font-size: 25px; line-height: 1.1; }
  .contact__first { color: var(--orange); }
  .contact__last { color: var(--green); }
  .contact__role { font-size: 16px; margin-top: 2px; }
  .contact__rule { width: 26px; height: 2px; background: var(--green); margin: 12px 0 10px 22px; }
  .contact__line { display: flex; align-items: center; gap: 10px; font-size: 16px; line-height: 1.7; }
  .contact__line svg { width: 15px; height: 15px; flex: none; }
</style>
</head>
<body>
<main class="canvas">

  <section class="card card--front" aria-label="Card front">
    <div class="brand"><span class="brand__mark"></span><span class="brand__name">QAL-VUB</span></div>
    <p class="tagline">Quicker Analog Launches &amp; Verified Unit Bring-up for Every Wafer</p>
  </section>

  <section class="card card--back" aria-label="Card back">
    <svg class="curve" viewBox="0 0 620 354" aria-hidden="true">
      <path d="M160 0 C240 190 430 230 620 130 V0 Z" fill="#ffffff"/>
      <path d="M160 0 C240 190 430 230 585 152" fill="none" stroke="#7bbb2a" stroke-width="7"/>
      <polygon points="570,134 612,138 586,168" fill="#7bbb2a"/>
    </svg>
    <div class="brand"><span class="brand__mark"></span><span class="brand__name">QAL-VUB</span></div>

    <div class="contact">
      <p class="contact__name"><span class="contact__first">Daniel K</span> <span class="contact__last">Forde</span></p>
      <p class="contact__role">Owner</p>
      <div class="contact__rule"></div>
      <p class="contact__line">
        <svg viewBox="0 0 16 16" aria-hidden="true"><path d="M3 1h3l1.5 4-2 1.2a9 9 0 0 0 4.3 4.3L11 8.5l4 1.5v3a2 2 0 0 1-2 2A12 12 0 0 1 1 3a2 2 0 0 1 2-2z" fill="#f39419"/></svg>
        +1 555 613 0946
      </p>
      <p class="contact__line">
        <svg viewBox="0 0 16 16" aria-hidden="true"><rect x="1" y="3" width="14" height="10" rx="1" fill="#1f78c4"/><path d="M1.5 3.5 8 9l6.5-5.5" fill="none" stroke="#4b5a75" stroke-width="1.3"/></svg>
        daniel.forde@qal-vub.com
      </p>
      <p class="contact__line">
        <svg viewBox="0 0 16 16" aria-hidden="true"><path d="M8 1a5 5 0 0 1 5 5c0 4-5 9-5 9S3 10 3 6a5 5 0 0 1 5-5z" fill="#7bbb2a"/><circle cx="8" cy="6" r="2" fill="#4b5a75"/></svg>
        Harlow Springs, Oregon, USA
      </p>
    </div>
  </section>

</main>
</body>
</html>
```